CM Candle Tube Packaging Design

Website: www.corvelmare.example
IG: @corvel.mare
Tagline: Elevate Your Ambiance
My brand is a sophisticated brand with luxury candles made of coconut wax. Im looking for an upscale minimalist chic design.
Discover the transformative power of positive energy with Corvel Mare candles. Indulge in true luxury with our specially crafted coconut wax blend that not only ignites captivating scents but also embodies modern elegance and empowering elements.
At Corvel Mare we're committed to delivering a unique and exhilarating aromatic experience to all candle lovers. Each candle is meticulously handcrafted in small batches using luxury fragrance oils exclusively formulated for coconut wax.
Our candles are:
Clean-burning
Paraben-Free
Phthalate-Free
Skin-Safe
Pet-Friendly

```html
<!DOCTYPE html>
<html lang="en">
<head>
<meta charset="utf-8">
<title>Corvel Mare – Candle Label</title>
<link href="https://fonts.googleapis.com/css2?family=Poppins:wght@300;400&family=Pinyon+Script&display=swap" rel="stylesheet">
<style>
  :root {
    --backdrop: #434f43;
    --label-black: #000000;
    --ink-white: #ffffff;
    --gold: #c9a24a;
    --gold-light: #f3cf72;
    --gold-deep: #b07c22;
  }
  html, body {
    margin: 0;
    padding: 0;
    width: 1200px;
    height: 2824px;
    overflow: hidden;
    background: var(--backdrop);
  }
  h1, h2, p, ul { margin: 0; padding: 0; }
  .canvas {
    position: relative;
    width: 1200px;
    height: 2824px;
    background: var(--backdrop);
  }
  .label {
    position: absolute;
    left: 240px;
    top: 827px;
    width: 720px;
    height: 1170px;
    background: var(--label-black);
    box-shadow: 0 0 24px rgba(0,0,0,0.35);
    color: var(--ink-white);
    font-family: "Poppins", sans-serif;
  }
  .brand-name {
    position: absolute;
    top: 250px;
    left: 0;
    width: 100%;
    text-align: center;
    font-weight: 300;
    font-size: 56px;
    line-height: 60px;
    letter-spacing: 1px;
    white-space: nowrap;
  }
  .brand-descriptor {
    position: absolute;
    top: 322px;
    left: 0;
    width: 100%;
    display: flex;
    justify-content: center;
    align-items: center;
    gap: 16px;
    font-weight: 400;
    font-size: 16px;
    line-height: 20px;
    letter-spacing: 6px;
    white-space: nowrap;
  }
  .brand-descriptor .rule {
    width: 26px;
    height: 1.5px;
    background: var(--ink-white);
  }
  .brand-motto {
    position: absolute;
    top: 346px;
    left: 0;
    width: 100%;
    text-align: center;
    font-family: "Pinyon Script", cursive;
    font-size: 24px;
    line-height: 28px;
  }
  .gold-frame {
    position: absolute;
    left: 98px;
    top: 423px;
    width: 535px;
    height: 650px;
    box-sizing: border-box;
    border: 1.5px solid var(--gold);
  }
  .tagline {
    position: absolute;
    top: 450px;
    left: 0;
    width: 100%;
    text-align: center;
    font-family: "Pinyon Script", cursive;
    font-weight: 400;
    font-size: 96px;
    line-height: 88px;
    white-space: nowrap;
    background: linear-gradient(100deg, var(--gold-deep) 0%, var(--gold-light) 45%, var(--gold) 70%, var(--gold-deep) 100%);
    -webkit-background-clip: text;
    background-clip: text;
    color: transparent;
  }
  .tagline span { display: block; }
  .tagline .line-two { margin-left: -20px; }
  .divider {
    position: absolute;
    left: 138px;
    top: 635px;
    width: 452px;
    height: 1.5px;
    background: var(--gold);
  }
  .qualities {
    position: absolute;
    top: 660px;
    left: 0;
    width: 100%;
    list-style: none;
    text-align: center;
    font-weight: 400;
    font-size: 37px;
    line-height: 45px;
  }
  .product-info {
    position: absolute;
    top: 976px;
    left: 0;
    width: 100%;
    text-align: center;
    font-weight: 400;
    font-size: 23px;
    line-height: 35px;
  }
</style>
</head>
<body>
  <main class="canvas">
    <section class="label" aria-label="Corvel Mare candle label">
      <h1 class="brand-name">CORVEL MARE</h1>
      <div class="brand-descriptor">
        <span class="rule"></span>
        <span>HANDMADE CANDLES</span>
        <span class="rule"></span>
      </div>
      <p class="brand-motto">with purpose and love</p>

      <div class="gold-frame"></div>

      <h2 class="tagline">
        <span class="line-one">Elevate Your</span>
        <span class="line-two">Ambiance</span>
      </h2>

      <div class="divider"></div>

      <ul class="qualities">
        <li>Clean-burning</li>
        <li>Paraben-Free</li>
        <li>Phthalate-Free</li>
        <li>Skin-Safe</li>
        <li>Pet-Friendly</li>
      </ul>

      <div class="product-info">
        <p>COCONUT WAX CANDLE</p>
        <p>14OZ. (396G)</p>
      </div>
    </section>
  </main>
</body>
</html>
```